Construction business card

I need a new business card, they can connect with my logo, brand.
What we do is residential house , design and build
I like: Navy blue / black
I attached our logo, brand,
and, some idea for business card.

```html
<!DOCTYPE html>
<html lang="en">
<head>
<meta charset="UTF-8">
<title>Harrow Building Group – Business Card</title>
<link href="https://fonts.googleapis.com/css2?family=Oswald:wght@600&family=Poppins:wght@400;500;700&display=swap" rel="stylesheet">
<style>
  :root {
    --backdrop: #1e1e20;
    --card: #0d0d0e;
    --brand-blue: #4a7fd0;
    --ink-white: #f2f2f2;
    --ink-soft: #d9d9d9;
    --gloss: #2c2c2f;
  }
  html, body {
    margin: 0;
    width: 1200px;
    height: 900px;
    overflow: hidden;
    background: var(--backdrop);
    font-family: "Poppins", sans-serif;
  }
  .sheet {
    position: relative;
    width: 1200px;
    height: 900px;
  }
  .card {
    position: absolute;
    width: 580px;
    height: 352px;
    background: var(--card);
    box-shadow: 0 18px 40px rgba(0,0,0,0.55);
    border-radius: 3px;
  }
  .card--front { left: 90px; top: 70px; }
  .card--back { left: 530px; top: 478px; }

  /* Front */
  .wordmark {
    position: absolute;
    inset: 0;
    display: flex;
    align-items: center;
    justify-content: center;
    gap: 14px;
  }
  .wordmark__mark {
    width: 26px;
    height: 26px;
    background: var(--brand-blue);
  }
  .wordmark__name {
    font-weight: 700;
    font-size: 30px;
    letter-spacing: 1px;
    text-transform: uppercase;
    color: var(--ink-white);
  }

  /* Back */
  .contact {
    position: absolute;
    left: 46px;
    top: 96px;
    color: var(--ink-white);
  }
  .contact__name {
    font-family: "Oswald", sans-serif;
    font-weight: 600;
    font-size: 24px;
    text-transform: uppercase;
    color: var(--brand-blue);
    line-height: 1.1;
  }
  .contact__role {
    font-weight: 500;
    font-size: 16px;
    margin-bottom: 22px;
  }
  .contact__address {
    font-size: 15px;
    line-height: 1.4;
    color: var(--ink-soft);
    margin-bottom: 16px;
  }
  .contact__list {
    list-style: none;
    margin: 0;
    padding: 0;
  }
  .contact__item {
    display: flex;
    align-items: center;
    gap: 10px;
    font-size: 15px;
    line-height: 1.55;
    color: var(--ink-soft);
  }
  .contact__icon {
    width: 15px;
    height: 15px;
    flex: none;
  }
  .gloss-wordmark {
    position: absolute;
    right: 40px;
    top: 56px;
    display: flex;
    align-items: center;
    gap: 10px;
  }
  .gloss-wordmark__mark {
    width: 18px;
    height: 18px;
    background: var(--gloss);
  }
  .gloss-wordmark__name {
    font-weight: 700;
    font-size: 19px;
    text-transform: uppercase;
    letter-spacing: 1px;
    color: var(--gloss);
  }
</style>
</head>
<body>
<main class="sheet">

  <section class="card card--front" aria-label="Card front">
    <div class="wordmark">
      <span class="wordmark__mark"></span>
      <span class="wordmark__name">Harrow Building Group</span>
    </div>
  </section>

  <section class="card card--back" aria-label="Card back">
    <div class="gloss-wordmark">
      <span class="gloss-wordmark__mark"></span>
      <span class="gloss-wordmark__name">Harrow Building Group</span>
    </div>

    <div class="contact">
      <div class="contact__name">Dorian Welles</div>
      <div class="contact__role">Founder &amp; CEO</div>
      <div class="contact__address">48 Halden St,<br>Elmford, VIC 3190</div>
      <ul class="contact__list">
        <li class="contact__item">
          <svg class="contact__icon" viewBox="0 0 16 16" aria-hidden="true">
            <path fill="var(--brand-blue)" d="M3.2 1.5l2.3-.3 1.3 3.1-1.5 1.1c.7 1.6 1.9 2.9 3.5 3.6l1.1-1.5 3.1 1.3-.3 2.3c-.2.9-1 1.4-1.9 1.4C6 12.5 1.5 8 1.5 3.4c0-.9.6-1.7 1.7-1.9z"/>
          </svg>
          0400 555 018
        </li>
        <li class="contact__item">
          <svg class="contact__icon" viewBox="0 0 16 16" aria-hidden="true">
            <rect x="1" y="3" width="14" height="10" rx="1.5" fill="var(--brand-blue)"/>
            <path d="M1.5 4l6.5 5 6.5-5" fill="none" stroke="var(--card)" stroke-width="1.4"/>
          </svg>
          info@harrowbuildinggroup.com.au
        </li>
        <li class="contact__item">
          <svg class="contact__icon" viewBox="0 0 16 16" aria-hidden="true">
            <circle cx="8" cy="8" r="7" fill="var(--brand-blue)"/>
            <path d="M1 8h14M8 1c2.4 2.2 2.4 11.8 0 14M8 1c-2.4 2.2-2.4 11.8 0 14" fill="none" stroke="var(--card)" stroke-width="1"/>
          </svg>
          www.harrowbuildinggroup.com.au
        </li>
      </ul>
    </div>
  </section>

</main>
</body>
</html>
```